Carpet cleaning company focused on high quality needs business cards

We are a growing company that just merged with another company and need to design a new business card. We do both residential as well as commercial cleaning. We do carpet, tile & grout, upholstery, hard floors, and stain & pet odor removal. We treat our customers like family and strive to achieve outstanding results with every job.

```html
<!DOCTYPE html>
<html lang="en">
<head>
<meta charset="utf-8">
<title>Harborline Floor Care – Business Cards</title>
<link rel="stylesheet" href="https://fonts.googleapis.com/css2?family=Open+Sans:wght@400;600&display=swap">
<style>
  :root {
    --bg: #d9d9d9;
    --card: #ffffff;
    --ink: #1d1d1b;
    --blue: #0b7fc2;
    --red: #ef4a3e;
  }
  * { margin: 0; padding: 0; box-sizing: border-box; }
  html, body { width: 1200px; height: 588px; overflow: hidden; }
  body { background: var(--bg); font-family: "Open Sans", sans-serif; color: var(--ink); position: relative; }

  .card {
    position: absolute; top: 141px; width: 488px; height: 289px;
    background: var(--card); border-radius: 28px; overflow: hidden;
  }
  .card--left { left: 87px; }
  .card--right { left: 622px; }

  .brand { position: absolute; left: 40px; top: 127px; display: flex; align-items: center; gap: 10px; }
  .brand__dot { width: 30px; height: 30px; border-radius: 50%; background: var(--blue); flex: none; }
  .brand__name { font-weight: 600; font-size: 18px; line-height: 1.2; color: var(--ink); white-space: nowrap; }

  .divider { position: absolute; left: 280px; top: 75px; width: 2px; height: 137px; background: var(--blue); }

  .details { position: absolute; left: 296px; top: 70px; font-size: 13.5px; line-height: 1.3; }
  .details__name { font-size: 19px; font-weight: 600; color: var(--blue); line-height: 1.25; }
  .details__name span { color: var(--red); }
  .details__title { font-size: 13.5px; margin-bottom: 10px; }
  .contact { list-style: none; margin-bottom: 10px; }
  .contact li { display: flex; align-items: center; gap: 4px; height: 17px; white-space: nowrap; }
  .contact svg { width: 11px; height: 11px; fill: var(--blue); flex: none; }
  .address { font-style: normal; }

  .band { position: absolute; left: 0; right: 0; bottom: 0; }
  .card--left .band--main { height: 26px; background: var(--blue); }
  .card--left .band--rule { bottom: 30px; height: 4px; background: var(--red); }
  .card--right .band--main { height: 26px; background: var(--red); }
  .card--right .band--rule { bottom: 30px; height: 4px; background: var(--blue); }
</style>
</head>
<body>

  <section class="card card--left">
    <div class="brand">
      <div class="brand__dot"></div>
      <div class="brand__name">Harborline Floor Care</div>
    </div>
    <div class="divider"></div>
    <div class="details">
      <p class="details__name">Marla <span>Benton</span></p>
      <p class="details__title">Executive Director</p>
      <ul class="contact">
        <li><svg viewBox="0 0 24 24"><path d="M6.6 10.8a15.1 15.1 0 0 0 6.6 6.6l2.2-2.2a1 1 0 0 1 1-.25 11.4 11.4 0 0 0 3.6.57 1 1 0 0 1 1 1V20a1 1 0 0 1-1 1A17 17 0 0 1 3 4a1 1 0 0 1 1-1h3.5a1 1 0 0 1 1 1c0 1.25.2 2.45.57 3.57a1 1 0 0 1-.25 1z"/></svg>555 014 2287</li>
        <li><svg viewBox="0 0 24 24"><path d="M2 5h20v2l-10 6L2 7zM2 9.3l10 6 10-6V19H2z"/></svg>info@harborlinecare.com</li>
        <li><svg viewBox="0 0 24 24"><circle cx="12" cy="12" r="10"/></svg>www.harborlinecare.com</li>
      </ul>
      <address class="address">2270 Harbor Lane<br>Coral Springs,</address>
    </div>
    <div class="band band--rule"></div>
    <div class="band band--main"></div>
  </section>

  <section class="card card--right">
    <div class="brand">
      <div class="brand__dot"></div>
      <div class="brand__name">Harborline Floor Care</div>
    </div>
    <div class="divider"></div>
    <div class="details">
      <p class="details__name">Marla <span>Benton</span></p>
      <p class="details__title">Executive Director</p>
      <ul class="contact">
        <li><svg viewBox="0 0 24 24"><path d="M6.6 10.8a15.1 15.1 0 0 0 6.6 6.6l2.2-2.2a1 1 0 0 1 1-.25 11.4 11.4 0 0 0 3.6.57 1 1 0 0 1 1 1V20a1 1 0 0 1-1 1A17 17 0 0 1 3 4a1 1 0 0 1 1-1h3.5a1 1 0 0 1 1 1c0 1.25.2 2.45.57 3.57a1 1 0 0 1-.25 1z"/></svg>555 014 2287</li>
        <li><svg viewBox="0 0 24 24"><path d="M2 5h20v2l-10 6L2 7zM2 9.3l10 6 10-6V19H2z"/></svg>info@harborlinecare.com</li>
        <li><svg viewBox="0 0 24 24"><circle cx="12" cy="12" r="10"/></svg>www.harborlinecare.com</li>
      </ul>
      <address class="address">2270 Harbor Lane<br>Coral Springs,</address>
    </div>
    <div class="band band--rule"></div>
    <div class="band band--main"></div>
  </section>

</body>
</html>
```